We want to design total new business card and logo for Kestrel Building Services Ltd

Our company name Kestrel Building Services Ltd. Design new logo and business card , need hi-end luxury style art for architecture and construction industry. The card should simple but stylish. Our business focus on CONNECT tradesman to construction company, help marketing construction company tender oversea projects, managing franchise in construction sector, delivery amazing services to our client, so Logo should show the CONNECTION IDEA, CONNECTING PEOPLE, LUXURY. Visit our website for more information: kestrelgroup.example.nz

Target Market(s)

Directors or managers

Industry/Entity Type

Construction Company

Contact Information for Business Card

Name, Title, Mobile, Email, Website

Font styles to use
Serif

Colors

Designer to choose colors to be used in the design.

Requirements
Must have
• Simple and luxury, connection icon
Nice to have
• Special materials, plastic card, look through,...
• Look new ideas.

```html
<!DOCTYPE html>
<html lang="en">
<head>
<meta charset="UTF-8">
<title>Kestrel Building Services Ltd — Business Card</title>
<link rel="stylesheet" href="https://fonts.googleapis.com/css2?family=Cinzel:wght@600&family=Tinos:wght@400;700&display=swap">
<style>
  :root {
    --backdrop: #18191c;
    --card: #1f2427;
    --card-edge: #2a3034;
    --ink-light: #f2f2f2;
    --ink-muted: #d7dadc;
    --teal: #27b3c4;
    --teal-soft: #1e8ea0;
  }
  * { margin: 0; padding: 0; box-sizing: border-box; }
  html, body {
    width: 1200px; height: 800px; overflow: hidden;
    background: var(--backdrop);
  }
  .canvas {
    position: relative; width: 1200px; height: 800px;
    display: flex; align-items: center; justify-content: center; gap: 40px;
  }
  .card {
    position: relative; width: 540px; height: 310px;
    background: var(--card);
    border: 1px solid var(--card-edge);
    box-shadow: 0 18px 40px rgba(0,0,0,0.55);
  }

  /* Front */
  .card--front { display: flex; align-items: center; justify-content: center; }
  .brand {
    display: flex; flex-direction: column; align-items: center; gap: 14px;
  }
  .brand__dot {
    width: 62px; height: 62px; border-radius: 50%;
    background: var(--teal);
  }
  .brand__name {
    font-family: "Cinzel", serif; font-weight: 600;
    color: var(--ink-light); font-size: 21px; letter-spacing: 1.5px;
    text-align: center; line-height: 1.45;
    padding: 6px 10px;
    border-top: 1.5px solid var(--ink-light);
    border-bottom: 1.5px solid var(--ink-light);
  }

  /* Back */
  .card--back { display: flex; align-items: center; padding: 0 34px 0 40px; }
  .back__mark {
    flex: 0 0 190px; display: flex; flex-direction: column; align-items: center; gap: 12px;
  }
  .back__mark .brand__dot { width: 76px; height: 76px; }
  .back__mark-name {
    font-family: "Cinzel", serif; font-weight: 600;
    color: var(--teal); font-size: 13px; letter-spacing: 1px;
    text-align: center; line-height: 1.4;
  }
  .back__divider {
    width: 1px; height: 150px; background: var(--teal-soft);
    margin: 0 26px 0 16px;
  }
  .contact { font-family: "Tinos", serif; color: var(--ink-muted); }
  .contact__name {
    font-weight: 700; color: var(--teal); font-size: 25px; line-height: 1.05;
  }
  .contact__title { font-size: 14px; margin-bottom: 12px; }
  .contact__address { font-size: 13px; line-height: 1.4; margin-bottom: 12px; }
  .contact__list { list-style: none; font-size: 13px; line-height: 1.75; }
  .contact__list li { display: flex; align-items: center; gap: 8px; }
  .contact__icon { width: 15px; height: 15px; flex: 0 0 15px; }
  .contact__web span { color: var(--teal); }
</style>
</head>
<body>
<main class="canvas">
  <section class="card card--front" aria-label="Card front">
    <div class="brand">
      <div class="brand__dot"></div>
      <p class="brand__name">Kestrel<br>Building Services Ltd</p>
    </div>
  </section>

  <section class="card card--back" aria-label="Card back">
    <div class="back__mark">
      <div class="brand__dot"></div>
      <p class="back__mark-name">Kestrel Building<br>Services Ltd</p>
    </div>
    <div class="back__divider"></div>
    <div class="contact">
      <h1 class="contact__name">Daniel Hartley</h1>
      <p class="contact__title">Manager</p>
      <p class="contact__address">PO Box 482, Harbour Road<br>Riverside Lane, Auckland 1010</p>
      <ul class="contact__list">
        <li>
          <svg class="contact__icon" viewBox="0 0 16 16" aria-hidden="true">
            <circle cx="8" cy="8" r="7.2" fill="none" stroke="#27b3c4" stroke-width="1.2"/>
            <path d="M5.6 4.6l1.3 1.6-.8.9c.5 1 1.2 1.7 2.2 2.2l.9-.8 1.6 1.3-.7 1.2c-2.6-.4-4.7-2.5-5.1-5.1z" fill="#27b3c4"/>
          </svg>
          0400 555 218
        </li>
        <li>
          <svg class="contact__icon" viewBox="0 0 16 16" aria-hidden="true">
            <circle cx="8" cy="8" r="7.2" fill="none" stroke="#27b3c4" stroke-width="1.2"/>
            <rect x="4.3" y="5.3" width="7.4" height="5.4" fill="none" stroke="#27b3c4" stroke-width="1"/>
            <path d="M4.3 5.3L8 8.4l3.7-3.1" fill="none" stroke="#27b3c4" stroke-width="1"/>
          </svg>
          info@kestrelgroup.example.nz
        </li>
        <li class="contact__web">
          <svg class="contact__icon" viewBox="0 0 16 16" aria-hidden="true">
            <circle cx="8" cy="8" r="7.2" fill="none" stroke="#27b3c4" stroke-width="1.2"/>
            <circle cx="8" cy="8" r="3.8" fill="none" stroke="#27b3c4" stroke-width="1"/>
            <path d="M4.2 8h7.6M8 4.2c-1.6 2.3-1.6 5.3 0 7.6M8 4.2c1.6 2.3 1.6 5.3 0 7.6" fill="none" stroke="#27b3c4" stroke-width="0.9"/>
          </svg>
          www.<span>kestrelgroup.example.nz</span>
        </li>
      </ul>
    </div>
  </section>
</main>
</body>
</html>
```